New Business Card Design Project

Need a design that will create an impact / strong impression towards our clients for our business. We are in the lighting business and we do lighting retrofits for large commercial to industrial clientele.

Target Market(s)

Lighting Industry

Industry/Entity Type

Business

Font styles to use
Other font styles liked:
• we would like to use the font on our logo, not sure what it is though..

Requirements
Must have
• Our logo.
Nice to have
• We are open to suggestions that have to do with lighting.

```html
<!DOCTYPE html>
<html lang="en">
<head>
<meta charset="utf-8">
<title>Kestrel Lighting Co. — Business Card</title>
<link rel="stylesheet" href="https://fonts.googleapis.com/css2?family=Roboto:wght@400;500;700&display=swap">
<style>
  :root{
    --bg:#2b2b2b;
    --card:#f4f4f2;
    --green-deep:#0f3d12;
    --green-dark:#1a5c1e;
    --green-mid:#0c8a38;
    --green-light:#6cc75d;
    --ink-grey:#555;
    --white:#ffffff;
  }
  *{margin:0;padding:0;box-sizing:border-box}
  html,body{width:1200px;height:886px;overflow:hidden}
  body{background:var(--bg);font-family:"Roboto",Arial,sans-serif;position:relative}
  .card{position:absolute;width:540px;height:310px;background:var(--card);border-radius:22px;overflow:hidden;box-shadow:0 10px 30px rgba(0,0,0,.45)}
  .card--front{left:60px;top:110px}
  .card--back{left:600px;top:460px}

  .brand{position:absolute;text-align:left}
  .brand__name{display:flex;align-items:center;gap:8px;font-weight:700;font-size:26px;color:var(--green-dark);letter-spacing:.5px}
  .brand__mark{width:14px;height:14px;background:var(--green-light)}
  .brand__rule{height:2px;background:var(--green-dark);margin:6px 0 4px}
  .brand__url{font-size:13px;color:var(--ink-grey)}
  .card--front .brand{right:34px;top:34px}

  .feature-art{position:absolute;left:22px;right:22px;top:150px;height:140px;border-radius:0 0 6px 6px;
    background:linear-gradient(90deg,var(--green-deep) 0%,var(--green-mid) 35%,var(--green-light) 55%,var(--green-deep) 70%,var(--green-mid) 85%,var(--green-light) 100%)}

  .card--back .brand{right:34px;top:40px}
  .band{position:absolute;left:0;top:0;width:540px;height:310px}
  .band-art{position:absolute;left:204px;top:176px;width:64px;height:14px;
    background:linear-gradient(90deg,var(--green-light),var(--green-mid),var(--green-light))}

  .person{position:absolute;left:28px;top:198px;color:var(--white)}
  .person__name{font-weight:700;font-size:20px;line-height:22px;text-transform:uppercase;letter-spacing:.3px}
  .person__role{font-size:12px;line-height:14px;text-transform:uppercase;margin:1px 0 4px 14px}
  .contact{list-style:none;font-size:12px;line-height:14px;margin-left:14px}
  .contact li{display:flex;align-items:center;gap:8px}
  .contact svg{width:11px;height:11px;fill:var(--white)}

  .address{position:absolute;right:28px;top:162px;text-align:right;color:var(--white);font-size:12.5px;line-height:16px;font-style:normal}
</style>
</head>
<body>

<section class="card card--front">
  <div class="brand">
    <div class="brand__name"><span class="brand__mark"></span>Kestrel Lighting Co.</div>
    <div class="brand__rule"></div>
    <div class="brand__url">www.kestrellighting.com</div>
  </div>
  <div class="feature-art" role="img" aria-label="Large stepped green graphic in dark, mid and light greens"></div>
</section>

<section class="card card--back">
  <svg class="band" viewBox="0 0 540 310" aria-hidden="true">
    <defs>
      <linearGradient id="bandFill" x1="0" y1="0" x2="1" y2="1">
        <stop offset="0" stop-color="#1f6b22"/>
        <stop offset="1" stop-color="#0f3d12"/>
      </linearGradient>
    </defs>
    <path d="M0 190 L240 190 L540 95 L540 310 L0 310 Z" fill="url(#bandFill)"/>
  </svg>
  <div class="band-art" role="img" aria-label="Small stepped green graphic"></div>

  <div class="brand">
    <div class="brand__name"><span class="brand__mark"></span>Kestrel Lighting Co.</div>
    <div class="brand__rule"></div>
  </div>

  <div class="person">
    <div class="person__name">Dana Whitfield</div>
    <div class="person__role">CEO/Founder</div>
    <ul class="contact">
      <li><svg viewBox="0 0 12 12"><path d="M2 1l2 0 1 3-1.5 1a6 6 0 0 0 3.5 3.5L8 7l3 1v2a1 1 0 0 1-1 1A9 9 0 0 1 1 2a1 1 0 0 1 1-1z"/></svg>555 210 4471</li>
      <li><svg viewBox="0 0 12 12"><path d="M3 0h6a1 1 0 0 1 1 1v10a1 1 0 0 1-1 1H3a1 1 0 0 1-1-1V1a1 1 0 0 1 1-1zm0 2v7h6V2z"/></svg>555 318 6620</li>
      <li><svg viewBox="0 0 12 12"><path d="M3 0h6v3H3zM1 4h10v5H9v3H3V9H1zm3 4v3h4V8z"/></svg>555 742 0953</li>
      <li><svg viewBox="0 0 12 12"><path d="M0 2h12v8H0zm1 1v.3l5 3.2 5-3.2V3z"/></svg>dana@kestrellighting.com</li>
    </ul>
  </div>

  <address class="address">
    214 Alder Court<br>
    Fairview, Oregon 97024<br>
    www.kestrellighting.com
  </address>
</section>

</body>
</html>
```